Business Cards for new orthopaedic surgery practice

My husband and I are starting our own orthopaedic surgery practice. We are looking for a business card that is uniform, but one will have my name/title and the other will have his. You can just create one design with my name on it for now. But when I choose your design as the winning design I will ask that you add another copy with his name/title.

We are looking for classy, simple, elite all in one. We like dark blues/a little gold/yellow. Something that goes with our logo. We want our logo incorporated. Here is all the info you need:
Business name: RV Bone & Vitality Center
Location: 38517 North Willowmere Ave
Palm Hollow, FL 33498
Phone: 954-218-4063
Fax: 954-582-7341
Email: info@myrvbonecare.example

Names: Lydia Vance, M.D.
Board Certified Hand and Upper Extremity Surgeon

Ebo Dansu, M.D.
Board Certified Hip & Knee Replacement/General Orthopaedic Surgeon

Can decide what you want to put on the back. Maybe a slogan:
Grounded in Care. Centered on You

I am just going to upload our logo. The only thing is if we select you as the winning design, the location, and phone numbers may change. We will need your help to update that once fully solidified.

Industry/Entity Type

Medical

Contact Information for Business Card

Colors
0054AA
0677BA
7BADD7
CADEEF
E8F1F8
0094D4
00A9DD
6FCCEA
C7EBF8
E9F6FB

Requirements
Must have
• class, appeal,
Should not have
• We want to air on the side of masculine if we are looking at masculine vs. feminine feel. But we still want it classy, sophisticated, and something we will love

```html
<!DOCTYPE html>
<html lang="en">
<head>
<meta charset="utf-8">
<title>RV Bone &amp; Vitality Center — Business Card</title>
<link rel="stylesheet" href="https://fonts.googleapis.com/css2?family=Tinos:wght@400;700&display=swap">
<style>
  :root {
    --navy: #1b2850;
    --navy-deep: #151f40;
    --gold: #c9a24f;
    --gold-light: #dcbb72;
    --paper: #f7f7f6;
    --ink: #5a5a5a;
    --backdrop: #e6e6e4;
  }
  * { margin: 0; padding: 0; box-sizing: border-box; }
  html, body { width: 1200px; height: 801px; overflow: hidden; }
  body {
    background: var(--backdrop);
    font-family: "Tinos", "Times New Roman", serif;
    position: relative;
  }
  .card {
    position: absolute;
    top: 246px;
    width: 540px;
    height: 309px;
    overflow: hidden;
    border: 3px solid var(--gold);
    box-shadow: 0 10px 24px rgba(0,0,0,0.18);
  }
  .card--front { left: 45px; background: var(--paper); }
  .card--back { left: 615px; background: var(--navy); }

  .front-shape { position: absolute; inset: 0; }

  .brand-name {
    position: absolute;
    color: #ffffff;
    font-weight: 700;
    text-align: center;
    letter-spacing: 1px;
    line-height: 1.15;
  }
  .card--front .brand-name { left: 300px; top: 62px; width: 200px; font-size: 22px; }
  .card--back .brand-name { left: 0; right: 0; top: 92px; font-size: 28px; }

  .contact { position: absolute; left: 26px; top: 122px; color: var(--ink); }
  .contact__name { color: var(--gold); font-weight: 700; font-size: 22px; }
  .contact__title { font-size: 14px; line-height: 1.2; margin-top: 2px; }
  .contact__list { list-style: none; margin-top: 14px; font-size: 14px; line-height: 1.3; }
  .contact__list li { display: flex; align-items: center; gap: 7px; }
  .contact__list svg { width: 12px; height: 12px; fill: var(--gold); flex: none; }
  .contact__address { font-style: normal; font-size: 14px; line-height: 1.25; margin-top: 12px; }

  .slogan-band {
    position: absolute;
    left: 0; right: 0; top: 228px;
    height: 30px;
    background: linear-gradient(90deg, rgba(201,162,79,0) 0%, var(--gold) 20%, var(--gold-light) 50%, var(--gold) 80%, rgba(201,162,79,0) 100%);
    display: flex; align-items: center; justify-content: center;
  }
  .slogan {
    color: var(--navy);
    font-weight: 700;
    font-size: 17px;
    letter-spacing: 0.5px;
  }
</style>
</head>
<body>

<section class="card card--front" aria-label="Business card front">
  <svg class="front-shape" viewBox="0 0 534 303" aria-hidden="true">
    <circle cx="392" cy="38" r="182" fill="var(--gold)"/>
    <circle cx="399" cy="32" r="180" fill="var(--navy)"/>
  </svg>
  <p class="brand-name">RV Bone &amp;<br>Vitality Center</p>

  <div class="contact">
    <h1 class="contact__name">Lydia Vance, M.D.</h1>
    <p class="contact__title">Board Certified Hand and<br>Upper Extremity Surgeon</p>
    <ul class="contact__list">
      <li><svg viewBox="0 0 12 12"><path d="M2.5 1h2l1 3-1.4 1a6 6 0 0 0 2.9 2.9l1-1.4 3 1v2a1 1 0 0 1-1 1A9.5 9.5 0 0 1 1.5 2a1 1 0 0 1 1-1z"/></svg>954-218-4063</li>
      <li><svg viewBox="0 0 12 12"><path d="M3 0h5l1 1v3H3zM1 5h10v5H9v2H3v-2H1zm3 3v3h4V8z"/></svg>954-582-7341</li>
      <li><svg viewBox="0 0 12 12"><path d="M0 2h12v8H0zm1 1v.5l5 3.5 5-3.5V3z"/></svg>info@myrvbonecare.example</li>
    </ul>
    <address class="contact__address">38517 North Willowmere Ave<br>Palm Hollow, FL 33498</address>
  </div>
</section>

<section class="card card--back" aria-label="Business card back">
  <p class="brand-name">RV Bone &amp;<br>Vitality Center</p>
  <div class="slogan-band">
    <p class="slogan">Grounded in Care. Centered on You</p>
  </div>
</section>

</body>
</html>
```